Harborview Estates Business Card for Apartment Buildings

Create business cards for resident managers who run apartment buildings. The audience is the public who are searching for apartment rentals, and current residents who live at the apartment building. Key design element will be incorporating the company logo, however, the logo cannot dominate. The building name and manager name are more important than the logo. Current business card design leaves little room for copy, so we may need to reduce the size on the current card to allow for more space for copy.

Target Market(s)

Adults 18-65 years of age, who are looking for an apartment rental, plus current residents who live at our apartment buildings.

Industry/Entity Type

Property Management

Contact Information for Business Card

A major design element will be use of the company logo. Important property and manager contact information must be part of the design. The size of the logo will need to be reduced to make room for building and manager contact copy.

Font styles to use
Sans Serif

Colors
3176b5
000000
959595
ffffff

Requirements
Must have
• 1) Incorporate the company logo.
• 2) Use the company colors (dark blue, black/grey, over white).
• 3) FEATURE THE BUILDING NAME
• 4) FEATURE THE MANAGER NAME
• 5) The company name is less important than BUILDING and MANAGER
• 6) Manager contact information
• **SEE ATTACHED CREATIVE BRIEF**
Nice to have
• 1) Back of card logo watermark
• 2) Ability to write notes on back of carfd
Should not have
• Avoid letting the company logo dominate the card, the building name and manager are more important than the company logo.

```html
<!DOCTYPE html>
<html lang="en">
<head>
<meta charset="utf-8">
<title>Harborview Estates – Resident Manager Card</title>
<link rel="stylesheet" href="https://fonts.googleapis.com/css2?family=Roboto:wght@400;700&display=swap">
<style>
  :root {
    --brand-blue: #0a6aa8;
    --arc-grey: #46484b;
    --paper: #ffffff;
    --backdrop: #e6e6e6;
    --ink-white: #ffffff;
  }
  * { margin: 0; padding: 0; box-sizing: border-box; }
  html, body { width: 1200px; height: 960px; overflow: hidden; }
  body {
    background: var(--backdrop);
    font-family: "Roboto", Arial, sans-serif;
    position: relative;
  }
  .card {
    position: absolute;
    left: 280px;
    width: 656px;
    height: 374px;
    background: var(--paper);
    box-shadow: 0 3px 10px rgba(0,0,0,0.25);
    overflow: hidden;
  }
  .card--front { top: 80px; }
  .card--back { top: 506px; }

  .front-art { position: absolute; inset: 0; width: 100%; height: 100%; }

  .manager { position: absolute; left: 58px; top: 62px; color: var(--ink-white); }
  .manager__name { font-size: 21px; font-weight: 700; letter-spacing: 0.1px; }
  .manager__title { font-size: 15.5px; font-weight: 400; margin-top: 2px; }

  .property { position: absolute; left: 58px; top: 141px; color: var(--ink-white); font-size: 14.5px; line-height: 22px; }
  .property__name { font-weight: 700; font-size: 14.5px; }

  .contacts { position: absolute; left: 58px; top: 226px; list-style: none; color: var(--ink-white); font-size: 15px; line-height: 22px; }
  .contacts li { display: flex; align-items: center; gap: 9px; }
  .contacts svg { width: 15px; height: 15px; flex: none; }

  .company-name {
    position: absolute;
    left: 398px;
    top: 160px;
    color: var(--brand-blue);
    font-weight: 700;
    font-size: 36px;
    line-height: 36px;
    letter-spacing: -0.5px;
    text-transform: uppercase;
  }

  .back-brand {
    position: absolute;
    left: 56px;
    top: 62px;
    display: flex;
    align-items: center;
    gap: 10px;
  }
  .back-brand__dot { width: 20px; height: 20px; border-radius: 50%; background: var(--brand-blue); }
  .back-brand__name {
    color: var(--brand-blue);
    font-weight: 700;
    font-size: 27px;
    text-transform: uppercase;
    letter-spacing: -0.3px;
  }
</style>
</head>
<body>

<section class="card card--front" aria-label="Business card front">
  <svg class="front-art" viewBox="0 0 711 405" preserveAspectRatio="none" aria-hidden="true">
    <rect width="711" height="405" fill="var(--brand-blue)"/>
    <path d="M468 0 C330 30 270 240 420 405 L711 405 L711 0 Z" fill="var(--paper)"/>
    <path d="M655 30 C520 -25 330 40 326 215 C324 300 380 370 442 405 L436 405 C360 350 320 270 336 190 C360 60 520 5 655 30 Z" fill="var(--arc-grey)"/>
  </svg>

  <div class="manager">
    <p class="manager__name">Marisol Delgado</p>
    <p class="manager__title">Resident Manager</p>
  </div>

  <address class="property" style="font-style:normal">
    <p class="property__name">Cedar Court Apartments</p>
    <p>2458 Linden Avenue</p>
    <p>Bayside, CA 90412</p>
  </address>

  <ul class="contacts">
    <li>
      <svg viewBox="0 0 16 16" aria-label="Phone"><path d="M4 1 L6.5 4 L5 6 C6 8.5 7.5 10 10 11 L12 9.5 L15 12 L13 15 C7 14.5 1.5 9 1 3 Z" fill="#fff"/></svg>
      <span>555-201-4830</span>
    </li>
    <li>
      <svg viewBox="0 0 16 16" aria-label="Fax"><rect x="1" y="6" width="14" height="7" rx="1.5" fill="#fff"/><rect x="4" y="2" width="8" height="4" fill="#fff"/><rect x="4" y="11" width="8" height="4" fill="#fff" stroke="var(--brand-blue)" stroke-width="1"/></svg>
      <span>555-201-4831</span>
    </li>
    <li>
      <svg viewBox="0 0 16 16" aria-label="Mobile"><rect x="1" y="3" width="14" height="10" fill="#fff"/><path d="M1 3 L8 9 L15 3" fill="none" stroke="var(--brand-blue)" stroke-width="1.2"/></svg>
      <span>555-201-4832</span>
    </li>
    <li>
      <svg viewBox="0 0 16 16" aria-label="Email"><g fill="none" stroke="#fff" stroke-width="1.2"><circle cx="8" cy="8" r="6.5"/><ellipse cx="8" cy="8" rx="3" ry="6.5"/><path d="M1.5 8 H14.5 M2.5 4.7 H13.5 M2.5 11.3 H13.5"/></g></svg>
      <span>marisol@harborviewest.com</span>
    </li>
  </ul>

  <p class="company-name">Harborview<br>Estates</p>
</section>

<section class="card card--back" aria-label="Business card back">
  <div class="back-brand">
    <span class="back-brand__dot"></span>
    <span class="back-brand__name">Harborview Estates</span>
  </div>
</section>

</body>
</html>
```